Meridale Bed Company Needs Business Card

Looking for a very nice looking business card. Creative but not extravagant. We sell beds and pillows across the U.S. and need something professional but catchy. I have attached the logo.

Name : Devin Holt
Title : President
Phone : (800) 471-2960
Email: sleep@quilmora.com
Website: www.quilmora.com

Can be single-sided or double-sided
horizontal or vertical

Can use Blues/Greys

Target Market(s)

Mass Market

Industry/Entity Type

Retail

Contact Information for Business Card

Name : Devin Holt
Title : President
Phone : (800) 471-2960
Email: sleep@quilmora.com
Website: www.quilmora.com

Requirements
Must have
• Clean, Modern, Smooth
• Can use Blues/Greys
• On the other side without the information - have something simple like www.quilmora.com or our logo
Nice to have
• Surprise me
Should not have
• Nothing crazy, nothing cluttered

```html
<!DOCTYPE html>
<html lang="en">
<head>
<meta charset="utf-8">
<title>Quilmora Business Card</title>
<link rel="stylesheet" href="https://fonts.googleapis.com/css2?family=Montserrat:wght@400;500;600&display=swap">
<style>
  :root {
    --page-bg: #2b2b2d;
    --card-black: #050505;
    --brand-blue: #2aa6df;
    --ink-white: #ffffff;
    --rule-grey: #d9d9d9;
  }
  * { margin: 0; padding: 0; box-sizing: border-box; }
  html, body {
    width: 1200px;
    height: 900px;
    overflow: hidden;
    background: var(--page-bg);
    font-family: "Montserrat", Arial, sans-serif;
  }
  .stage {
    position: relative;
    width: 1200px;
    height: 900px;
  }
  .card {
    position: absolute;
    left: 250px;
    width: 700px;
    height: 400px;
    background: var(--card-black);
    border-radius: 26px;
    overflow: hidden;
    box-shadow: 0 10px 30px rgba(0,0,0,0.45);
  }
  .card--front { top: 35px; }
  .card--back { top: 465px; }

  .brand-name {
    font-weight: 500;
    color: var(--brand-blue);
    line-height: 1;
    white-space: nowrap;
  }
  .card--front .brand-name {
    position: absolute;
    top: 150px;
    width: 100%;
    text-align: center;
    font-size: 80px;
  }
  .card--front .site-url {
    position: absolute;
    bottom: 48px;
    width: 100%;
    text-align: center;
    font-size: 21px;
    font-weight: 400;
    color: var(--ink-white);
  }
  .site-url .accent { color: var(--brand-blue); }

  .card--back .brand-name {
    position: absolute;
    left: 60px;
    top: 150px;
    font-size: 64px;
  }
  .holder {
    position: absolute;
    right: 58px;
    top: 190px;
    text-align right;
    text-align: right;
  }
  .holder-name {
    font-size: 27px;
    font-weight: 600;
    color: var(--brand-blue);
    line-height: 30px;
  }
  .holder-title {
    font-size: 15px;
    font-weight: 400;
    color: var(--ink-white);
    line-height: 18px;
  }
  .edge-notch {
    position: absolute;
    right: -22px;
    top: 176px;
    width: 44px;
    height: 44px;
    border-radius: 50%;
    background: var(--ink-white);
  }
  .divider {
    position: absolute;
    left: 150px;
    right: 44px;
    top: 246px;
    height: 2px;
    background: var(--rule-grey);
  }
  .contact-list {
    position: absolute;
    left: 150px;
    top: 268px;
    list-style: none;
  }
  .contact-item {
    display: flex;
    align-items: center;
    gap: 10px;
    font-size: 20px;
    line-height: 27px;
    color: var(--ink-white);
  }
  .contact-item svg { width: 14px; height: 14px; fill: var(--brand-blue); }
  .base-band {
    position: absolute;
    left: 0;
    right: 0;
    bottom: 0;
    height: 14px;
    display: flex;
  }
  .base-band .band-blue { flex: 0 0 50%; background: var(--brand-blue); }
  .base-band .band-white { flex: 1; background: var(--ink-white); }
</style>
</head>
<body>
<main class="stage">
  <section class="card card--front">
    <div class="brand-name">Quilmora</div>
    <div class="site-url">www.<span class="accent">quilmora</span>.com</div>
  </section>

  <section class="card card--back">
    <div class="brand-name">Quilmora</div>
    <span class="edge-notch"></span>
    <div class="holder">
      <div class="holder-name">Devin Holt</div>
      <div class="holder-title">President</div>
    </div>
    <div class="divider"></div>
    <ul class="contact-list">
      <li class="contact-item">
        <svg viewBox="0 0 24 24" aria-hidden="true"><path d="M6.6 10.8a15 15 0 0 0 6.6 6.6l2.2-2.2a1 1 0 0 1 1-.25 11.4 11.4 0 0 0 3.6.6 1 1 0 0 1 1 1V20a1 1 0 0 1-1 1A17 17 0 0 1 3 4a1 1 0 0 1 1-1h3.5a1 1 0 0 1 1 1c0 1.25.2 2.45.6 3.6a1 1 0 0 1-.25 1z"/></svg>
        (800) 471-2960
      </li>
      <li class="contact-item">
        <svg viewBox="0 0 24 24" aria-hidden="true"><path d="M2 5h20v14H2zm2 2v.5l8 5 8-5V7zm0 2.8V17h16V9.8l-8 5z"/></svg>
        sleep@quilmora.com
      </li>
      <li class="contact-item">
        <svg viewBox="0 0 24 24" aria-hidden="true"><path d="M12 2a10 10 0 1 0 0 20 10 10 0 0 0 0-20zm6.9 6h-3a15 15 0 0 0-1.3-3.9A8 8 0 0 1 18.9 8zM12 4c.8 1.1 1.5 2.5 1.9 4h-3.8c.4-1.5 1.1-2.9 1.9-4zM4.3 14a8 8 0 0 1 0-4h3.4a16 16 0 0 0 0 4zm.8 2h3a15 15 0 0 0 1.3 3.9A8 8 0 0 1 5.1 16zm3-8h-3a8 8 0 0 1 4.3-3.9A15 15 0 0 0 8.1 8zM12 20c-.8-1.1-1.5-2.5-1.9-4h3.8c-.4 1.5-1.1 2.9-1.9 4zm2.3-6H9.7a14 14 0 0 1 0-4h4.6a14 14 0 0 1 0 4zm.3 5.9a15 15 0 0 0 1.3-3.9h3a8 8 0 0 1-4.3 3.9zm1.7-5.9a16 16 0 0 0 0-4h3.4a8 8 0 0 1 0 4z"/></svg>
        www.quilmora.com
      </li>
    </ul>
    <div class="base-band"><span class="band-blue"></span><span class="band-white"></span></div>
  </section>
</main>
</body>
</html>
```